Harbourline Electrical Solutions

On one side. LOGO (underneath:) Commercial Industrial Residential

- NAME & CONTACT DETAILS

Marcus T. Hollings
Project Manager

(Cell icon) (441) 555-0187
(Email icon) hlelectricalsolutions@mailvento.com
(Facebook & Instagram icons )@hlelectricalsolutions

Other side: LOGO - underneath ELECTRICAL CONSTRUCTION & MAINTENANCE . LED LIGHTING & AUTOMATION . LIFE SAFETY SYSTEMS (FIRE ALARM / SECURITY) . DATA & COMMUNICATION

```html
<!DOCTYPE html>
<html lang="en">
<head>
<meta charset="utf-8">
<title>Harbourline Electrical Solutions – Business Card</title>
<link href="https://fonts.googleapis.com/css2?family=Montserrat:wght@500;600&family=Poppins:wght@400;500;600&display=swap" rel="stylesheet">
<style>
  :root {
    --teal: #135a6e;
    --grey: #4d4d4f;
    --white: #ffffff;
    --backdrop: #e9ecee;
  }
  * { box-sizing: border-box; margin: 0; padding: 0; }
  html, body { width: 1200px; height: 880px; overflow: hidden; }
  body {
    background: var(--backdrop);
    font-family: "Poppins", sans-serif;
    position: relative;
  }
  .card {
    position: absolute;
    width: 630px;
    height: 360px;
    background: var(--white);
    border-radius: 22px;
    overflow: hidden;
    box-shadow: 0 10px 30px rgba(0,0,0,0.15);
  }
  .card--services { left: 200px; top: 60px; }
  .card--contact { left: 370px; top: 460px; }

  .brand {
    display: flex;
    align-items: center;
    gap: 14px;
    position: absolute;
  }
  .brand__square {
    width: 40px; height: 40px;
    background: var(--teal);
  }
  .brand__name {
    font-family: "Montserrat", sans-serif;
    font-weight: 600;
    color: var(--teal);
    text-transform: uppercase;
    letter-spacing: 3px;
    line-height: 1.15;
    font-size: 22px;
  }
  .card--services .brand { left: 150px; top: 92px; }

  .services {
    position: absolute;
    left: 40px; right: 40px; top: 236px;
    text-align: center;
    color: var(--teal);
    font-size: 15px;
    font-weight: 500;
    line-height: 1.6;
  }

  .card__waves { position: absolute; inset: 0; }

  .card--contact .brand { left: 42px; top: 90px; }
  .brand__name--small { font-size: 19px; }
  .sectors {
    position: absolute;
    left: 42px; top: 186px;
    color: var(--grey);
    font-size: 15px;
    font-weight: 500;
    letter-spacing: 0.5px;
  }

  .contact {
    position: absolute;
    right: 26px; top: 78px;
    text-align: right;
    color: var(--white);
  }
  .contact__name {
    font-family: "Montserrat", sans-serif;
    font-weight: 600;
    font-size: 17px;
    letter-spacing: 1px;
    text-transform: uppercase;
    line-height: 1.3;
  }
  .contact__role { font-size: 13px; margin-bottom: 18px; }
  .contact__line {
    display: flex;
    align-items: center;
    justify-content: flex-end;
    gap: 8px;
    font-size: 12px;
    line-height: 2;
  }
  .icon {
    width: 17px; height: 17px;
    border-radius: 50%;
    background: var(--white);
    display: inline-flex;
    align-items: center;
    justify-content: center;
    flex: none;
  }
  .icon svg { width: 11px; height: 11px; }
</style>
</head>
<body>

<section class="card card--services" aria-label="Card back: services">
  <div class="brand">
    <span class="brand__square"></span>
    <span class="brand__name">Harbourline<br>Electrical<br>Solutions</span>
  </div>
  <p class="services">
    Electrical Construction &amp; Maintenance | LED Lighting &amp; Automation<br>
    Life Safety Systems (FIRE ALARM / SECURITY) | Data &amp; Communication
  </p>
</section>

<section class="card card--contact" aria-label="Card front: contact">
  <svg class="card__waves" viewBox="0 0 630 360" aria-hidden="true">
    <path d="M270 222 C 265 290, 190 325, 60 332 L 60 348 C 210 346, 285 300, 270 222 Z" fill="var(--grey)"/>
    <path d="M520 0 C 420 40, 380 100, 340 160 C 300 230, 240 320, 140 360 L 630 360 L 630 0 Z" fill="var(--teal)"/>
    <path d="M492 8 C 400 50, 360 110, 318 172 C 280 240, 220 318, 112 352" fill="none" stroke="var(--white)" stroke-width="0"/>
  </svg>

  <div class="brand">
    <span class="brand__square"></span>
    <span class="brand__name brand__name--small">Harbourline<br>Electrical<br>Solutions</span>
  </div>
  <p class="sectors">Commercial Industrial Residential</p>

  <div class="contact">
    <p class="contact__name">Marcus T. Hollings</p>
    <p class="contact__role">Project Manager</p>
    <p class="contact__line">(441) 555-0187
      <span class="icon"><svg viewBox="0 0 12 12"><rect x="3.5" y="1" width="5" height="10" rx="1" fill="var(--teal)"/></svg></span>
    </p>
    <p class="contact__line">hlelectricalsolutions@mailvento.com
      <span class="icon"><svg viewBox="0 0 12 12"><rect x="1" y="3" width="10" height="6.5" fill="var(--teal)"/><path d="M1 3 L6 7 L11 3" fill="none" stroke="var(--white)" stroke-width="1"/></svg></span>
    </p>
    <p class="contact__line">@hlelectricalsolutions
      <span class="icon"></span><span class="icon"></span>
    </p>
  </div>
</section>

</body>
</html>
```